Health Supplement Series for 60 tablets of pure Amber Vine Core powder

We need a packaging design theme for a health supplement for international consumers. Our initial product is called 'Amber Vine Core'. It is for general health and is particularly effective for diabetic symptoms.
We would like to see designs that are clean and fresh.
It should give the impression of professional, premium pharmaceutical grade products.
Our company logo is attached below.

Target Market(s)

International

Industry/Entity Type

Health And Wellness

Font styles to use
Serif
Sans Serif

Requirements
Must have
• Bottle and box packaging required.
• 1st product is bottle of 60 tablets of 0.5gm each.
Should not have
• Seals and other "must buy" "guaranteed" etc

```html
<!DOCTYPE html>
<html lang="en">
<head>
<meta charset="utf-8">
<title>Verdant Labworks – Natural 60 tablets box</title>
<link href="https://fonts.googleapis.com/css2?family=Roboto+Condensed:wght@300;400;700&family=Montserrat:wght@500&display=swap" rel="stylesheet">
<style>
:root{
  --bg:#e6e6e6;
  --panel:#f8eeea;
  --panel-side:#efe4e0;
  --green-dark:#2f6a1f;
  --green-mid:#5c9a34;
  --green-light:#8cc63f;
  --brand:#6cbf2e;
  --ink:#111;
  --grey:#555;
}
*{margin:0;padding:0;box-sizing:border-box}
html,body{width:1200px;height:1200px;overflow:hidden;background:var(--bg)}
.canvas{position:relative;width:1200px;height:1200px}
.box{position:absolute;left:250px;top:160px;display:flex;height:880px;box-shadow:0 10px 30px rgba(0,0,0,.08)}
.side-panel{position:relative;width:230px;height:100%;background:var(--panel-side)}
.front-panel{position:relative;width:480px;height:100%;background:var(--panel)}
.marble{background:linear-gradient(160deg,var(--green-dark) 0%,var(--green-mid) 35%,var(--green-light) 55%,var(--green-mid) 75%,var(--green-dark) 100%)}
.green-band{position:absolute;left:225px;top:0;width:50px;height:100%}
.brand-label{position:absolute;left:90px;top:215px;width:310px;height:220px;padding:12px}
.brand-label-inner{width:100%;height:100%;background:#fff;display:flex;flex-direction:column;align-items:center;padding-top:36px}
.brand-lockup{display:flex;align-items:center;gap:10px}
.brand-mark{width:38px;height:46px;background:var(--brand)}
.brand-name{font-family:'Montserrat',sans-serif;font-weight:500;color:var(--brand);line-height:1.05}
.brand-name .big{display:block;font-size:33px;letter-spacing:3px}
.brand-name .small{display:block;font-size:14px;letter-spacing:.5px}
.variant{margin-top:24px;font-family:'Roboto Condensed',sans-serif;font-weight:700;font-size:20px;color:var(--grey);letter-spacing:.5px}
.count{margin-top:24px;font-family:'Roboto Condensed',sans-serif;font-weight:300;font-size:19px;color:var(--grey)}
.nutrition-frame{position:absolute;left:14px;top:175px;width:202px;padding:8px}
.nutrition{background:#fff;padding:6px 7px;font-family:'Roboto Condensed',sans-serif;color:var(--ink);font-size:10px;line-height:1.35}
.nutrition h2{font-size:29px;font-weight:700;line-height:1;letter-spacing:-.5px}
.rule-thick{border-top:7px solid var(--ink);margin:3px 0}
.rule-mid{border-top:3px solid var(--ink);margin:3px 0}
.row{display:flex;justify-content:space-between;border-top:1px solid #999}
.row.indent span:first-child{padding-left:10px}
.row b{font-weight:700}
.footnote{font-size:8px;line-height:1.3;margin-top:4px}
.dv-table{width:100%;font-size:8px;border-collapse:collapse;margin-top:4px}
.dv-table td{padding:0 1px}
</style>
</head>
<body>
<div class="canvas">
  <div class="box">
    <section class="side-panel">
      <div class="nutrition-frame marble">
        <div class="nutrition">
          <h2>Nutrition Facts</h2>
          <div>Serving Size 4 Pieces</div>
          <div class="rule-thick"></div>
          <div><b>Amount Per Serving</b></div>
          <div class="row"><span><b>Calories</b> 110</span><span></span></div>
          <div class="rule-mid"></div>
          <div class="row"><span></span><span><b>% Daily Value*</b></span></div>
          <div class="row"><span><b>Total Fat</b> 2.5g</span><b>4%</b></div>
          <div class="row indent"><span>Saturated Fat 1g</span><b>5%</b></div>
          <div class="row indent"><span>Trans Fat 0g</span><b></b></div>
          <div class="row"><span><b>Cholesterol</b> 0mg</span><b>0%</b></div>
          <div class="row"><span><b>Sodium</b> 170mg</span><b>7%</b></div>
          <div class="row"><span><b>Total Carbohydrate</b> 21g</span><b>7%</b></div>
          <div class="row indent"><span>Dietary Fiber 0g</span><b>0%</b></div>
          <div class="row indent"><span>Sugars 13g</span><b></b></div>
          <div class="row"><span><b>Protein</b> 0g</span><b></b></div>
          <div class="rule-thick"></div>
          <div class="row"><span></span><b>0%</b></div>
          <p class="footnote">*Percent Daily Values are based on a 2,000 calorie diet. Your Daily Values may be higher or lower depending on your calorie needs.</p>
          <table class="dv-table">
            <tr><td></td><td>Calories</td><td>2,000</td><td>2,500</td></tr>
            <tr><td>Total Fat</td><td>Less than</td><td>65g</td><td>80g</td></tr>
            <tr><td>Sat Fat</td><td>Less than</td><td>20g</td><td>25g</td></tr>
            <tr><td>Cholesterol</td><td>Less than</td><td>300mg</td><td>300mg</td></tr>
            <tr><td>Sodium</td><td>Less than</td><td>2400mg</td><td>2400mg</td></tr>
            <tr><td>Total Carb</td><td></td><td>300g</td><td>375g</td></tr>
            <tr><td>Dietary Fiber</td><td></td><td>25g</td><td>30g</td></tr>
          </table>
        </div>
      </div>
    </section>
    <section class="front-panel">
      <div class="green-band marble" role="img" aria-label="Green marbled swirl pattern band"></div>
      <div class="brand-label marble">
        <div class="brand-label-inner">
          <div class="brand-lockup">
            <div class="brand-mark"></div>
            <div class="brand-name"><span class="big">VERDANT</span><span class="small">LABWORKS LIMITED</span></div>
          </div>
          <div class="variant">NATURAL</div>
          <div class="count">60 tablets</div>
        </div>
      </div>
    </section>
  </div>
</div>
</body>
</html>
```